Velvet Harbor Snout Sticks - our own unique product line of cotton swabs

We have something now that we are not too happy with. Looking to create a label for a line of cotton swabs that we have created and designed to clean your nose from mucus and boogers. The logo that i have so far for the packaging is the white background with the black silhouette nose (attached). We need something that can do well in the retail/consumer market. Our website address (even though it is not live yet) should be listed somewhere on the label....
www.VelvetHarborGoods.example ( we sell pillows, but we have other product lines)
We would also like to see a brief description on how to correctly use the nose pick on the back side of the label. The description on how to use should read " insert cotton nose pick into nostril and give it a few counter clock wise twirls or till you feel mucus/debris latch onto the cotton. You may need to repeat the process and use more than one nose pick to achieve desired result."
As well as a warning mentioning : "Never insert plastic end of nose pick into any part of your body. Be careful and use with caution."
Also for you to know, the cotton is made from 100% natural cotton, the cotton head itself is thick and highly absorbent making it a pleasure to use. There are 50 nose picks per pack.
We're fine with keeping it simple and not making the packaging too busy, however we're open to your ideas and designs! I have given you the most important information relevant to the project. If there are any questions or something is not clear enough please kindly message me.

Requirements
Must have
• professional looking
clean looking
not busy
Should not have
• words clumping together making it appear as too much text in one area
too much text clumped together on the design

```html
<!DOCTYPE html>
<html lang="en">
<head>
<meta charset="utf-8">
<title>Velvet Harbor Snout Sticks – Label</title>
<link rel="stylesheet" href="https://fonts.googleapis.com/css2?family=Montserrat:wght@300;400;500;600;700;800&family=Kaushan+Script&display=swap">
<style>
  :root {
    --teal: #3fbfb4;
    --grey: #7b8489;
    --grey-dark: #6c7479;
    --paper: #ffffff;
    --stage: #ffffff;
    --rule: #9aa1a5;
  }
  * { box-sizing: border-box; margin: 0; padding: 0; }
  html, body {
    width: 1200px; height: 589px; overflow: hidden;
    background: var(--stage);
    font-family: "Montserrat", sans-serif;
  }
  .canvas { position: relative; width: 1200px; height: 589px; }

  /* ---------- Front label ---------- */
  .front-label {
    position: absolute; left: 30px; top: 62px;
    width: 803px; height: 603px;
    transform: scale(0.772); transform-origin: top left;
    background: var(--paper);
    border: 1.5px solid var(--rule);
    overflow: hidden;
  }
  .brand-name {
    position: absolute; left: 58px; top: 52px;
    font-size: 60px; font-weight: 500; color: var(--grey);
    letter-spacing: -0.5px; line-height: 1;
  }
  .claim-badge {
    position: absolute; left: 616px; top: 105px;
    width: 124px; height: 124px; border-radius: 50%;
    border: 2px solid var(--teal); background: #eaf7f6;
  }
  .nose-art {
    position: absolute; left: 40px; top: 185px;
    width: 220px; height: 310px;
    background: linear-gradient(160deg, #eef0f1 0%, #dfe3e5 100%);
    border-radius: 0 110px 40px 60px;
  }
  .cotton-claim {
    position: absolute; left: 195px; top: 242px;
    font-size: 27px; font-weight: 700; color: var(--grey-dark);
    letter-spacing: 2.5px;
  }
  .product-band {
    position: absolute; left: 165px; top: 278px;
    width: 638px; height: 112px; background: var(--teal);
    color: #fff; text-align: center;
  }
  .product-name {
    display: block; padding-left: 30px; margin-top: 10px;
    font-size: 68px; font-weight: 700; letter-spacing: 4px; line-height: 1;
  }
  .product-purpose {
    display: block; padding-left: 30px; margin-top: 10px;
    font-size: 18px; font-weight: 700; letter-spacing: 0.2px;
  }
  .tagline {
    position: absolute; left: 292px; top: 398px;
    font-family: "Kaushan Script", cursive;
    font-size: 40px; color: var(--grey-dark);
  }
  .tagline-rule {
    position: absolute; left: 300px; top: 458px;
    width: 462px; height: 8px; background: var(--grey);
  }
  .pack-count {
    position: absolute; right: 62px; top: 470px;
    text-align: center; color: var(--grey-dark); line-height: 1;
  }
  .pack-count .num { display: block; font-size: 74px; font-weight: 800; }
  .pack-count .unit { display: block; font-size: 30px; font-weight: 600; margin-top: -2px; }
  .site-url {
    position: absolute; left: 52px; top: 537px;
    font-size: 25px; font-weight: 500; color: var(--teal); letter-spacing: 1.2px;
  }

  /* ---------- Back label ---------- */
  .back-label {
    position: absolute; left: 680px; top: 185px;
    width: 722px; height: 322px;
    transform: scale(0.68); transform-origin: top left;
    background: var(--paper);
    border: 1.5px solid var(--rule);
  }
  .step-icon {
    position: absolute; left: 50px;
    width: 90px; height: 90px; border-radius: 50%;
    border: 3px solid var(--teal); background: #f2faf9;
  }
  .step-icon.one { top: 20px; }
  .step-icon.two { top: 117px; }
  .step-icon.three { top: 213px; }
  .howto-title {
    position: absolute; left: 165px; top: 36px; width: 507px;
    display: flex; align-items: center; gap: 8px;
    font-size: 21px; font-weight: 700; color: var(--teal); letter-spacing: 1px;
  }
  .howto-title::before, .howto-title::after {
    content: ""; flex: 1; border-top: 3px dotted var(--teal);
  }
  .howto-text {
    position: absolute; left: 165px; top: 73px; width: 507px;
    font-size: 19.5px; font-weight: 400; color: var(--grey);
    line-height: 28.5px; text-align: justify;
  }
  .warning-pill {
    position: absolute; left: 160px; top: 230px;
    width: 515px; height: 56px; border-radius: 10px;
    background: var(--teal); color: #fff;
    font-size: 17px; font-weight: 500; line-height: 22px;
    display: flex; align-items: center; justify-content: center; text-align: center;
  }
</style>
</head>
<body>
<main class="canvas">

  <section class="front-label" aria-label="Front label">
    <div class="brand-name">Velvet Harbor</div>
    <div class="claim-badge" role="img" aria-label="Natural cotton, highly absorbent badge"></div>
    <div class="nose-art" role="img" aria-label="Grey nose silhouette illustration"></div>
    <div class="cotton-claim">100% NATURAL COTTON</div>
    <div class="product-band">
      <span class="product-name">SNOUT STICKS</span>
      <span class="product-purpose">CLEAN YOUR NOSE FROM MUCUS AND BOOGERS</span>
    </div>
    <div class="tagline">How do you pick your nose?</div>
    <div class="tagline-rule"></div>
    <div class="pack-count"><span class="num">50</span><span class="unit">count</span></div>
    <div class="site-url">www.VelvetHarborGoods.example</div>
  </section>

  <section class="back-label" aria-label="Back label">
    <div class="step-icon one" role="img" aria-label="Step 1: swab inserted into nostril"></div>
    <div class="step-icon two" role="img" aria-label="Step 2: twirl swab counter clockwise"></div>
    <div class="step-icon three" role="img" aria-label="Step 3: remove the used swab"></div>
    <h2 class="howto-title">HOW TO USE</h2>
    <p class="howto-text">Insert cotton nose pick into nostril and give it a few counter clock wise twirls or till you feel mucus/debris latch onto the cotton. You may need to repeat the process and use more than one nose pick to achieve desired result.</p>
    <p class="warning-pill">Never insert plastic end of nose pick into any part<br>of your body. Be careful and use with caution.</p>
  </section>

</main>
</body>
</html>
```